Fresh Dwelling Tract Guide needs a new Landing Page

I like to get a landing page or website with 2-3 pages to help target home buyers who are looking to buy homes from builders such as TW Residences, Morvik, P.L. Fennick, etc. The landing page/website to be non-cluttered and be able to explain to home buyers that there are many benefits to include me as their buyer's agent when they buy a brand new home from any builders.
I may want to incorporate a short explanation video (animated) on the landing page and then for the viewer to click on a button that will take them to another page where they can search for new homes from different builders.
Target Market(s)
Home buyers looking to buy brand new home from builders such as TW Residences, Morvik, P.L. Fennick, etc.
Industry/Entity Type
Real Estate
Number of Pages Required
2 page
Font styles to use
Requirements
Must have
- The landing page may have the explanation video at the bottom of the landing page (scrolled down) or there may be a CALL TO ACTION button that takes the viewer to the 2nd page to watch the explanation video. Once they watched the explanation video and are still interested, they can click on another CALL TO ACTION button that will take them to another website that they will be able to search for all the available new homes and register their contact information.
Should not have
- No clutters and no dark colors.

```html
<!DOCTYPE html>
<html lang="en">
<head>
<meta charset="utf-8">
<title>Fresh Dwelling Tract Guide — Neighbors Building Neighborhoods</title>
<link rel="stylesheet" href="https://fonts.googleapis.com/css2?family=Open+Sans:wght@400;600;700&family=Lora:wght@400&display=swap">
<style>
  :root {
    --pink: #c53f8c;
    --rose: #c23a5c;
    --rust: #a0463a;
    --white: #ffffff;
    --play-icon: #1a1a1a;
    --cta: #cc35c9;
    --sans: "Open Sans", Arial, sans-serif;
    --serif: "Lora", Georgia, serif;
  }
  * { margin: 0; padding: 0; box-sizing: border-box; }
  html, body { width: 1200px; height: 675px; overflow: hidden; }
  body { font-family: var(--sans); color: var(--white); }

  .hero {
    position: relative;
    width: 1200px;
    height: 675px;
    overflow: hidden;
  }
  .hero-photo {
    position: absolute;
    inset: 0;
    background:
      radial-gradient(ellipse at 50% 70%, rgba(150, 20, 50, 0.18) 0%, rgba(150, 20, 50, 0) 60%),
      linear-gradient(100deg, var(--pink) 0%, var(--rose) 50%, var(--rust) 100%);
  }

  .site-header {
    position: absolute;
    top: 0; left: 0; right: 0;
    height: 110px;
  }
  .brand {
    position: absolute;
    left: 47px;
    top: 30px;
    font-size: 47px;
    font-weight: 700;
    letter-spacing: -1px;
    line-height: 1;
  }
  .main-nav {
    position: absolute;
    top: 57px;
    left: 383px;
    display: flex;
    gap: 30px;
    font-size: 11.5px;
    font-weight: 400;
    list-style: none;
    white-space: nowrap;
  }
  .main-nav li { position: relative; }
  .main-nav .is-active::after {
    content: "";
    position: absolute;
    left: 0; right: 0;
    bottom: -8px;
    height: 2px;
    background: var(--white);
  }
  .social {
    position: absolute;
    top: 57px;
    left: 1018px;
    display: flex;
    gap: 14px;
    font-size: 11.5px;
    font-weight: 600;
    list-style: none;
    white-space: nowrap;
  }

  .headline {
    position: absolute;
    top: 200px;
    left: 0; right: 0;
    text-align: center;
    font-size: 73px;
    font-weight: 700;
    line-height: 100px;
    letter-spacing: 0;
    text-shadow: 0 4px 24px rgba(90, 10, 40, 0.35);
  }
  .tagline {
    position: absolute;
    top: 411px;
    left: 0; right: 0;
    text-align: center;
    font-family: var(--serif);
    font-size: 17.5px;
  }
  .play-button {
    position: absolute;
    left: 575px;
    top: 470px;
    width: 48px;
    height: 48px;
  }
  .cta-button {
    position: absolute;
    left: 509px;
    top: 562px;
    width: 182px;
    height: 54px;
    background: var(--cta);
    display: flex;
    align-items: center;
    justify-content: center;
    font-size: 12px;
    font-weight: 700;
    letter-spacing: 1.6px;
    text-transform: uppercase;
  }
</style>
</head>
<body>
  <section class="hero">
    <div class="hero-photo" role="img" aria-label="Upward view of a modern building with a triangular peak, tinted in a pink to rust gradient"></div>

    <header class="site-header">
      <div class="brand">logo</div>
      <ul class="main-nav">
        <li class="is-active">Home</li>
        <li>How We Help</li>
        <li>Who We Help</li>
        <li>Client Successes</li>
        <li>Technology</li>
        <li>Resources</li>
        <li>Company</li>
      </ul>
      <ul class="social">
        <li>Chirper</li>
        <li>Friendbook</li>
      </ul>
    </header>

    <h1 class="headline">NEIGHBORS BUILDING<br>NEIGHBORHOODS</h1>
    <p class="tagline">Get the service you deserved</p>

    <svg class="play-button" viewBox="0 0 48 48" aria-label="Play video">
      <circle cx="24" cy="24" r="24" fill="var(--white)"/>
      <polygon points="19,15 33,24 19,33" fill="var(--play-icon)"/>
    </svg>

    <div class="cta-button">Get Started</div>
  </section>
</body>
</html>
```